VORLAND COMPOSITES INC website in USA

VORLAND COMPOSITES INC incorporated and operated in USA needs a completely new design of website. This Wyoming based company is a importer and distributor of composites material to supply mainly to American and Canadian/Mexican customers. Our main products includes Carbon Fiber, Aramid Fiber, Glass Fiber, Basalt Fiber, High Silica Glass, Quartz Fiber, S-Glass, Alumina Fiber, Vacuum Auxiliary.

We are one stop composites solution provider for Automotive, Aerospace, Construction, Electrical and Machinery industries.

We are exclusive sales company in North America for BLORAN composites produced from China and their other Asia facilities.

Target Market(s)

USA and Canada

Industry/Entity Type

Composites materials

Coding

Coded - Design and coding required

Number of Pages Required

5+ page

Requirements
Nice to have
• Color theme to match our corporate logo VORLAND. VORLAND stands for Northgate Provisioning Trade Holdings

```html
<!DOCTYPE html>
<html lang="en">
<head>
<meta charset="utf-8">
<title>VORLAND COMPOSITES INC — Website Design</title>
<link rel="stylesheet" href="https://fonts.googleapis.com/css2?family=Montserrat:wght@300;400;500;600;700&family=Inter:wght@400;500;600&display=swap">
<style>
:root{
  --navy:#0d2150;
  --orange:#f5950f;
  --orange-deep:#e8880a;
  --cream:#fdf1df;
  --ink:#1d1d1f;
  --muted:#55575c;
  --dark:#1b1b1d;
  --dark-2:#242426;
  --white:#ffffff;
  --head:'Montserrat',sans-serif;
  --body:'Inter',sans-serif;
}
*{box-sizing:border-box;margin:0;padding:0}
html,body{width:1200px;height:2310px;overflow:hidden;background:var(--navy)}
body{position:relative;font-family:var(--body);color:var(--ink)}
.abs{position:absolute}
.frame{position:absolute;background:var(--white);overflow:hidden}
.desktop{left:95px;top:95px;width:665px;height:2132px}
.mobile{left:821px;top:95px;width:284px;height:2215px}

/* photo stand-ins */
.photo-hero{background:radial-gradient(ellipse at 35% 45%,#8a6a4e 0%,#4a3d33 40%,#2a2826 75%,#1c1c1c 100%)}
.photo-shade{background:linear-gradient(180deg,rgba(20,20,22,.25),rgba(20,20,22,.55))}
.photo-circle{border-radius:50%;background:radial-gradient(circle at 40% 40%,#5a5a5c,#3b3b3d 70%,#2f2f31)}
.swatch{overflow:hidden}
.sw-carbon{background:linear-gradient(180deg,#d9d9d9 0%,#bdbdbd 22%,#4a4a4c 30%,#2a2a2c 70%,#3e3e40 100%)}
.sw-aramid{background:linear-gradient(180deg,#d9d9d9 0%,#bdbdbd 22%,#8d7a45 30%,#a8924f 65%,#6f5f35 100%)}
.sw-glass{background:linear-gradient(180deg,#d9d9d9 0%,#bdbdbd 22%,#5a5a5c 30%,#444446 70%,#5f5f61 100%)}
.sw-basalt{background:linear-gradient(180deg,#e0e0e0 0%,#c8c8c8 22%,#b8b3a0 30%,#cfc9b4 65%,#a9a48f 100%)}
.swatch-label{position:absolute;left:13px;bottom:10px;font-family:var(--head);font-size:11px;color:var(--white)}
.swatch-label b{font-weight:700}
.raised{box-shadow:0 6px 14px rgba(0,0,0,.3)}
.photo-team{background:linear-gradient(90deg,rgba(36,36,38,0) 0%,#4b4540 30%,#6b5f52 60%,#8d8070 100%)}

/* brand */
.brand{display:flex;align-items:center;gap:7px}
.brand-dot{width:12px;height:12px;border-radius:50%;border:2px solid var(--orange)}
.brand-name{font-family:var(--head);font-weight:700;color:var(--white);letter-spacing:.5px}
.brand-note{font-family:var(--body);color:var(--white);font-size:4.5px;line-height:1.35;border-left:1px solid rgba(255,255,255,.6);padding-left:5px;width:62px}

/* nav */
.nav{display:flex;gap:15px;font-size:6.2px;color:var(--white);align-items:center}
.btn-outline-sm{border:1px solid var(--white);color:var(--white);font-size:6px;padding:7px 11px}

/* type */
.hero-title{font-family:var(--head);font-weight:300;color:var(--white);text-align:center;line-height:1.02}
.hero-sub{font-size:7.6px;color:#e6e6e6;text-align:center;line-height:1.75}
.btn{position:absolute;display:flex;align-items:center;justify-content:center;font-family:var(--head);font-weight:600;letter-spacing:1px;font-size:7px;color:var(--white)}
.btn-fill{background:var(--orange)}
.btn-ghost{border:1px solid var(--white)}
.eyebrow{font-size:8px;color:var(--orange);display:flex;align-items:center;gap:6px;letter-spacing:.2px}
.eyebrow i{display:inline-block;width:24px;height:1px;background:var(--orange)}
.title{font-family:var(--head);font-weight:400;line-height:1.15}
.body-text{font-size:7.4px;line-height:1.8;color:var(--ink)}
.center{text-align:center;justify-content:center}
.feature{display:flex;align-items:center;gap:9px;font-size:6.8px;line-height:1.6;color:var(--muted)}
.ring{width:24px;height:24px;border-radius:50%;border-left:2px solid var(--orange);border-bottom:1px solid rgba(245,149,15,.4);display:flex;align-items:center;justify-content:center}
.ring span{width:8px;height:8px;border:1.3px solid var(--orange);border-radius:50% 0 50% 0}

.dark{background:var(--dark)}
.industry{position:absolute;width:90px;text-align:center;color:var(--white);font-family:var(--head);font-size:10.5px}
.ind-icon{width:36px;height:34px;margin:0 auto 8px;border-left:2.5px solid var(--orange);border-top:1px solid transparent;border-radius:50%;display:flex;align-items:center;justify-content:center}
.ind-icon span{width:12px;height:12px;border:1.3px solid var(--white);border-radius:2px}

.foot-h{font-family:var(--head);font-size:10px;color:var(--white)}
.foot-t{font-size:7.4px;color:#c9c9c9;line-height:1.85}
.foot-link{position:absolute;font-size:7.4px;color:#c9c9c9}
.social{width:17px;height:17px;border-radius:50%;background:#3a3a3c;display:inline-flex;align-items:center;justify-content:center;margin-right:9px}
.social span{width:5px;height:5px;border-radius:50%;background:var(--white)}
.hamburger span{display:block;width:16px;height:2px;background:var(--white);margin-bottom:3.5px}
</style>
</head>
<body>

<!-- ================= DESKTOP ================= -->
<section class="frame desktop" aria-label="Desktop home page">
  <!-- hero -->
  <div class="abs photo-hero" role="img" aria-label="Engineer in hard hat and safety vest in a composites warehouse" style="left:0;top:0;width:665px;height:440px"></div>
  <div class="abs photo-shade" style="left:0;top:0;width:665px;height:440px"></div>
  <svg class="abs" style="left:0;top:270px" width="665" height="200" viewBox="0 0 665 200">
    <path d="M0 140 C150 210 430 150 665 55 L665 200 L0 200 Z" fill="var(--white)"/>
    <path d="M0 138 C160 200 420 150 665 50 L665 82 C430 180 160 225 0 150 Z" fill="var(--orange)"/>
    <path d="M560 90 C610 70 640 55 665 40 L665 82 C630 100 590 115 555 125 Z" fill="var(--orange)"/>
  </svg>

  <div class="abs brand" style="left:52px;top:14px">
    <span class="brand-dot"></span><span class="brand-name" style="font-size:15px">VORLAND</span>
    <span class="brand-note">Northgate Provisioning Trade Holdings</span>
  </div>
  <nav class="abs nav" style="left:225px;top:20px">
    <span>Home</span><span>Products ▾</span><span>Industries</span><span>About us</span><span>Partners</span><span>Contact Us</span><span>◎ EN / FR</span>
  </nav>
  <div class="abs btn-outline-sm" style="left:539px;top:12px">Request a Quote</div>

  <h1 class="abs hero-title" style="left:100px;top:112px;width:465px;font-size:33px">High-Performance Composite Materials for North America</h1>
  <p class="abs hero-sub" style="left:130px;top:220px;width:405px">Supplying Carbon Fiber, Aramid, Glass, and Advanced Composites for Automotive, Aerospace, and Industrial Applications.</p>
  <div class="btn btn-fill" style="left:203px;top:288px;width:128px;height:28px">EXPLORE PRODUCTS</div>
  <div class="btn btn-ghost" style="left:342px;top:288px;width:119px;height:28px">REQUEST A QUOTE</div>

  <!-- about -->
  <svg class="abs" style="left:0;top:660px" width="665" height="140" viewBox="0 0 665 140">
    <path d="M0 20 C180 80 470 80 665 0 L665 8 C470 100 200 160 0 80 Z" fill="var(--cream)"/>
  </svg>
  <div class="abs" style="left:55px;top:459px;width:220px;height:220px;border-radius:50%;background:var(--orange)"></div>
  <div class="abs" style="left:65px;top:464px;width:218px;height:218px;border-radius:50%;background:var(--white)"></div>
  <div class="abs photo-circle" role="img" aria-label="Hands exchanging a carbon fiber sample" style="left:69px;top:467px;width:211px;height:211px"></div>
  <div class="abs brand" style="left:92px;top:560px">
    <span class="brand-dot"></span><span class="brand-name" style="font-size:20px">VORLAND</span>
    <span class="brand-note" style="font-size:5.5px;width:72px">Northgate Provisioning Trade Holdings</span>
  </div>

  <div class="abs eyebrow" style="left:322px;top:477px"><i></i>WHO WE ARE <span style="font-size:12px">★</span></div>
  <h2 class="abs title" style="left:322px;top:494px;width:320px;font-size:24px">Your Trusted Composites Distribution Partner</h2>
  <p class="abs body-text" style="left:322px;top:563px;width:270px">VORLAND COMPOSITES INC is a Wyoming-based distributor of premium composite materials across North America. We supply carbon, aramid, glass, basalt, and quartz fibers for industries like automotive, aerospace, and construction.</p>
  <div class="abs feature" style="left:328px;top:636px"><div class="ring"><span></span></div>Sustainable &amp; Eco-<br>Friendly Solutions</div>
  <div class="abs feature" style="left:466px;top:636px"><div class="ring"><span></span></div>High-Performance &amp;<br>Lightweight Materials</div>

  <!-- products -->
  <div class="abs eyebrow center" style="left:0;top:823px;width:665px"><i></i>OUR PRODUCTS<i></i></div>
  <h2 class="abs title" style="left:0;top:839px;width:665px;text-align:center;font-size:24px">Our Composite Materials</h2>
  <p class="abs body-text" style="left:190px;top:869px;width:285px;text-align:center">We supply high-performance fibers and advanced materials engineered for strength, precision, and performance.</p>

  <div class="abs swatch sw-carbon" role="img" aria-label="Carbon fiber weave close-up" style="left:55px;top:943px;width:128px;height:172px"><span class="swatch-label"><b>Carbon</b> Fiber</span></div>
  <div class="abs swatch sw-aramid" role="img" aria-label="Aramid fiber weave close-up" style="left:198px;top:943px;width:127px;height:172px"><span class="swatch-label"><b>Aramid</b> Fiber</span></div>
  <div class="abs swatch sw-glass raised" role="img" aria-label="Glass fiber weave close-up" style="left:340px;top:927px;width:127px;height:172px">
    <span class="abs" style="left:51px;top:73px;width:24px;height:24px;border:1.5px solid rgba(255,255,255,.7);border-radius:50%"></span>
    <span class="swatch-label"><b>Glass</b> Fiber</span></div>
  <div class="abs swatch sw-basalt" role="img" aria-label="Basalt fiber weave close-up" style="left:482px;top:943px;width:128px;height:172px"><span class="swatch-label"><b>Basalt</b> Fiber</span></div>
  <div class="btn btn-fill" style="left:279px;top:1140px;width:107px;height:28px">ALL MATERIALS</div>

  <!-- industries -->
  <svg class="abs" style="left:0;top:1200px" width="665" height="130" viewBox="0 0 665 130">
    <path d="M0 85 C200 -10 470 -20 665 75 L665 130 L0 130 Z" fill="var(--orange)"/>
    <path d="M0 160 C200 30 470 20 665 82 L665 130 L0 130 Z" fill="var(--dark)"/>
  </svg>
  <div class="abs dark" style="left:0;top:1328px;width:665px;height:804px"></div>

  <div class="abs eyebrow center" style="left:0;top:1341px;width:665px"><i></i>INDUSTRIES SERVED<i></i></div>
  <h2 class="abs title" style="left:0;top:1356px;width:665px;text-align:center;font-size:24px;color:var(--white)">Serving Innovation Across Industries</h2>
  <p class="abs body-text" style="left:160px;top:1392px;width:345px;text-align:center;color:#d8d8d8">Our advanced composite materials are trusted across multiple industries delivering strength, lightness, and performance where it matters most.</p>

  <div class="industry" style="left:64px;top:1455px"><div class="ind-icon"><span></span></div>Automotive</div>
  <div class="industry" style="left:175px;top:1455px"><div class="ind-icon"><span></span></div>Aerospace</div>
  <div class="industry" style="left:287px;top:1455px"><div class="ind-icon"><span></span></div>Construction</div>
  <div class="industry" style="left:398px;top:1455px"><div class="ind-icon"><span></span></div>Electrical</div>
  <div class="industry" style="left:509px;top:1455px"><div class="ind-icon"><span></span></div>Machinery</div>
  <div class="btn btn-fill" style="left:279px;top:1548px;width:107px;height:28px">ALL MATERIALS</div>

  <!-- cta -->
  <div class="abs" style="left:55px;top:1631px;width:554px;height:130px;background:var(--dark-2)"></div>
  <div class="abs photo-team" role="img" aria-label="Two colleagues in face masks reviewing documents" style="left:389px;top:1631px;width:220px;height:130px"></div>
  <h3 class="abs title" style="left:79px;top:1656px;font-size:16px;color:var(--white);font-weight:500">Ready to Source Premium Composites?</h3>
  <p class="abs" style="left:79px;top:1682px;font-size:7.4px;color:#cfcfcf">Contact our team for quotes, specifications, and partnership opportunities.</p>
  <div class="abs" style="left:79px;top:1710px;width:85px;height:25px;background:var(--white);font-size:7.6px;display:flex;align-items:center;justify-content:center">Contact Us &nbsp;→</div>

  <!-- footer -->
  <div class="abs brand" style="left:55px;top:1806px">
    <span class="brand-dot" style="width:16px;height:16px"></span><span class="brand-name" style="font-size:22px">VORLAND</span>
    <span class="brand-note" style="font-size:6px;width:78px">Northgate Provisioning Trade Holdings</span>
  </div>
  <p class="abs" style="left:285px;top:1790px;width:142px;font-size:6px;color:#d0d0d0;text-align:right;line-height:1.6">Lorem ipsum dolor sit amet, consectetur adipiscing elit</p>
  <div class="abs" style="left:434px;top:1788px;width:107px;height:25px;background:#333335;font-size:7.6px;color:#d0d0d0;padding:8px 10px">Your Email...</div>
  <div class="abs" style="left:541px;top:1788px;width:68px;height:25px;background:var(--orange);font-size:7.6px;color:var(--white);display:flex;align-items:center;justify-content:center">Join us &nbsp;→</div>

  <h4 class="abs foot-h" style="left:55px;top:1881px">About Us</h4>
  <p class="abs foot-t" style="left:55px;top:1900px;width:165px">lorem ipsum dolor sit amet, consectetur adipiscing elit, sed do eiusmod tempor incididunt ut labore et dolore magna aliqua.</p>
  <h4 class="abs foot-h" style="left:55px;top:1975px;color:var(--orange)">Do you need help?</h4>
  <p class="abs foot-t" style="left:55px;top:1994px">Our team is here to help you anytime:<br>+1 (555) 014 2290<br>help@vorlandsupply.com</p>

  <h4 class="abs foot-h" style="left:308px;top:1881px">Quick Links</h4>
  <span class="foot-link" style="left:308px;top:1908px">Home</span>
  <span class="foot-link" style="left:308px;top:1930px">About us</span>
  <span class="foot-link" style="left:308px;top:1953px">Testimonials</span>
  <span class="foot-link" style="left:308px;top:1975px">Services</span>
  <span class="foot-link" style="left:308px;top:1998px">Locations</span>
  <span class="foot-link" style="left:308px;top:2020px">Support</span>
  <span class="foot-link" style="left:397px;top:1908px">Resource Hub</span>
  <span class="foot-link" style="left:397px;top:1930px">Latest News</span>
  <span class="foot-link" style="left:397px;top:1953px">Our Services</span>
  <span class="foot-link" style="left:397px;top:1975px">Meet Team</span>
  <span class="foot-link" style="left:397px;top:1998px">Contact Us</span>
  <span class="foot-link" style="left:397px;top:2020px">Blog Insights</span>

  <h4 class="abs foot-h" style="left:513px;top:1881px">Services</h4>
  <span class="foot-link" style="left:513px;top:1908px">Explore Our Offerings</span>
  <span class="foot-link" style="left:513px;top:1930px">Learn More About Us</span>
  <span class="foot-link" style="left:513px;top:1953px">What Our Clients Say</span>
  <h4 class="abs foot-h" style="left:513px;top:1994px">Social Media</h4>
  <div class="abs" style="left:513px;top:2017px"><span class="social"><span></span></span><span class="social"><span></span></span><span class="social"><span></span></span><span class="social"><span></span></span></div>

  <p class="abs" style="left:55px;top:2102px;font-size:7.4px;color:#c9c9c9">VORLAND COMPOSITES INC © Copyright 2025, All Rights Reserved</p>
  <p class="abs" style="left:393px;top:2102px;font-size:7.4px;color:#c9c9c9">Privacy Policy &nbsp;| &nbsp;Terms &amp; Conditions &nbsp;| &nbsp;Cookie Policy</p>
</section>

<!-- ================= MOBILE ================= -->
<section class="frame mobile" aria-label="Mobile home page">
  <div class="abs photo-hero" role="img" aria-label="Engineer in hard hat and safety vest in a composites warehouse" style="left:0;top:0;width:284px;height:600px"></div>
  <div class="abs photo-shade" style="left:0;top:0;width:284px;height:600px"></div>
  <svg class="abs" style="left:0;top:520px" width="284" height="100" viewBox="0 0 284 100">
    <path d="M0 50 C90 95 210 80 284 30 L284 100 L0 100 Z" fill="var(--white)"/>
    <path d="M0 45 C90 85 210 70 284 0 L284 30 C210 85 90 100 0 60 Z" fill="var(--orange)"/>
  </svg>
  <div class="abs brand" style="left:14px;top:16px">
    <span class="brand-dot"></span><span class="brand-name" style="font-size:14px">VORLAND</span>
    <span class="brand-note" style="width:50px">Northgate Provisioning Trade Holdings</span>
  </div>
  <div class="abs hamburger" style="left:242px;top:19px"><span></span><span></span><span></span></div>

  <h1 class="abs hero-title" style="left:6px;top:324px;width:272px;font-size:24.5px">High-Performance Composite Materials for North America</h1>
  <p class="abs hero-sub" style="left:30px;top:415px;width:224px;color:var(--white)">Supplying Carbon Fiber, Aramid, Glass, and Advanced Composites for Automotive, Aerospace, and Industrial Applications.</p>
  <div class="btn btn-fill" style="left:77px;top:470px;width:128px;height:27px">EXPLORE PRODUCTS</div>
  <div class="btn btn-ghost" style="left:77px;top:509px;width:128px;height:27px">REQUEST A QUOTE</div>

  <div class="abs eyebrow" style="left:20px;top:624px"><i></i>WHO WE ARE <span style="font-size:12px">★</span></div>
  <h2 class="abs title" style="left:20px;top:640px;width:260px;font-size:19px">Your Trusted Composites Distribution Partner</h2>
  <p class="abs body-text" style="left:20px;top:699px;width:250px">VORLAND COMPOSITES INC is a Wyoming-based distributor of premium composite materials across North America. We supply carbon, aramid, glass, basalt, and quartz fibers for industries like automotive, aerospace, and construction.</p>
  <div class="abs feature" style="left:24px;top:760px"><div class="ring"><span></span></div>Sustainable &amp; Eco-<br>Friendly Solutions</div>
  <div class="abs feature" style="left:162px;top:760px"><div class="ring"><span></span></div>High-Performance &amp;<br>Lightweight Materials</div>

  <svg class="abs" style="left:0;top:1020px" width="284" height="70" viewBox="0 0 284 70">
    <path d="M0 5 C80 45 200 50 284 15 L284 20 C200 70 80 80 0 30 Z" fill="var(--cream)"/>
  </svg>
  <div class="abs" style="left:29px;top:820px;width:222px;height:222px;border-radius:50%;background:var(--orange)"></div>
  <div class="abs" style="left:40px;top:826px;width:216px;height:216px;border-radius:50%;background:var(--white)"></div>
  <div class="abs photo-circle" role="img" aria-label="Hands exchanging a carbon fiber sample" style="left:43px;top:829px;width:210px;height:210px"></div>
  <div class="abs brand" style="left:66px;top:920px">
    <span class="brand-dot"></span><span class="brand-name" style="font-size:19px">VORLAND</span>
    <span class="brand-note" style="font-size:5.5px;width:70px">Northgate Provisioning Trade Holdings</span>
  </div>

  <div class="abs eyebrow center" style="left:0;top:1140px;width:284px"><i></i>OUR PRODUCTS<i></i></div>
  <h2 class="abs title" style="left:0;top:1156px;width:284px;text-align:center;font-size:19px">Our Composite Materials</h2>
  <p class="abs body-text" style="left:18px;top:1186px;width:248px;text-align:center">We supply high-performance fibers and advanced materials engineered for strength, precision, and performance.</p>

  <div class="abs swatch sw-carbon" role="img" aria-label="Carbon fiber weave close-up" style="left:36px;top:1239px;width:212px;height:155px"><span class="swatch-label"><b>Carbon</b> Fiber</span></div>
  <div class="abs swatch sw-aramid" role="img" aria-label="Aramid fiber weave close-up" style="left:36px;top:1409px;width:212px;height:155px"><span class="swatch-label"><b>Aramid</b> Fiber</span></div>
  <div class="abs swatch sw-glass raised" role="img" aria-label="Glass fiber weave close-up" style="left:36px;top:1580px;width:212px;height:155px"><span class="swatch-label"><b>Glass</b> Fiber</span></div>
  <div class="abs swatch sw-basalt" role="img" aria-label="Basalt fiber weave close-up" style="left:36px;top:1750px;width:212px;height:155px"><span class="swatch-label"><b>Basalt</b> Fiber</span></div>

  <svg class="abs" style="left:0;top:1950px" width="284" height="70" viewBox="0 0 284 70">
    <path d="M0 30 C90 0 200 0 284 30 L284 70 L0 70 Z" fill="var(--orange)"/>
    <path d="M0 60 C90 20 200 15 284 40 L284 70 L0 70 Z" fill="var(--dark)"/>
  </svg>
  <div class="abs dark" style="left:0;top:2018px;width:284px;height:197px"></div>
  <div class="abs eyebrow center" style="left:0;top:2050px;width:284px"><i></i>INDUSTRIES SERVED<i></i></div>
  <h2 class="abs title" style="left:0;top:2066px;width:284px;text-align:center;font-size:19px;color:var(--white)">Serving Innovation Across Industries</h2>
  <p class="abs body-text" style="left:30px;top:2117px;width:224px;text-align:center;color:#d8d8d8">Our advanced composite materials are trusted across multiple industries delivering strength, lightness, and performance where it matters most.</p>
  <div class="industry" style="left:34px;top:2182px"><div class="ind-icon"><span></span></div></div>
  <div class="industry" style="left:118px;top:2182px"><div class="ind-icon"><span></span></div></div>
</section>

</body>
</html>
```